Budget Brand Responsive Website

Flat vector style website needed for value based IT support company. looking for clean, illustration intensive based design. Current test site can be found at www.bright-mend.co.uk and holding page it www.brightmend.co.uk this will show text and services, please feel free to use placeholder text if you think we need alternative text in places. Emphasis should be on low cost support and services listed on the site, would be nice to see costs in bold images. important colors are the blue, orange and white, see holding page and attached image of an advert

It Company

```html
<!DOCTYPE html>
<html lang="en">
<head>
<meta charset="utf-8">
<title>Bright Mend – IT Services</title>
<link href="https://fonts.googleapis.com/css2?family=Open+Sans:wght@400;600;700;800&display=swap" rel="stylesheet">
<style>
:root{
  --blue:#3b5aa3;
  --blue-dark:#2f4b8c;
  --navy:#1f3a75;
  --orange:#f07c1e;
  --orange-dark:#d9631a;
  --purple:#4a2b7d;
  --sky:#3f8fd4;
  --amber:#f5a623;
  --white:#ffffff;
  --light:#eef1f6;
  --text:#555b66;
  --heading:#2b2f38;
  --footer:#2c2c2e;
  --footer-dark:#1f1f21;
  --footer-text:#a6a8ad;
}
*{box-sizing:border-box;margin:0;padding:0}
html,body{width:1200px;height:2684px;overflow:hidden}
body{font-family:"Open Sans",Arial,sans-serif;color:var(--text);background:var(--white);position:relative}

.site-header{height:100px;display:flex;align-items:center;justify-content:space-between;padding:0 110px 0 60px;background:var(--white)}
.brand{display:flex;align-items:center;gap:14px}
.brand-square{width:34px;height:34px;background:var(--blue)}
.brand-name{font-size:36px;font-weight:800;color:var(--blue);letter-spacing:1px}
.main-nav{display:flex;gap:38px}
.main-nav a{font-size:15px;font-weight:700;color:var(--blue);text-decoration:none;padding-bottom:8px}
.main-nav a.active{border-bottom:3px solid var(--blue)}

.hero{height:420px;background:var(--blue);position:relative;text-align:center}
.hero-title{color:var(--white);font-size:50px;font-weight:800;padding-top:28px;letter-spacing:1px}
.hero-art{position:absolute;left:210px;top:120px;width:780px;height:280px;border-radius:12px;background:radial-gradient(ellipse at center,#5f80c6 0%,#4768b2 55%,var(--blue) 100%)}
.slider-arrow{position:absolute;top:195px;width:36px;height:56px;background:var(--navy);display:flex;align-items:center;justify-content:center}
.slider-arrow.prev{left:0}.slider-arrow.next{right:0}

.welcome{height:350px;text-align:center;padding-top:110px}
.section-title{font-size:34px;font-weight:800;color:var(--heading);letter-spacing:.5px}
.welcome p{font-size:13px;line-height:20px;width:900px;margin:22px auto 0}
.call-line{font-size:24px;font-weight:800;color:var(--blue);margin-top:34px}

.services{height:430px;background:var(--blue);padding-top:48px}
.services .section-title{color:var(--white);text-align:center}
.service-grid{display:grid;grid-template-columns:repeat(3,260px);column-gap:130px;row-gap:58px;justify-content:center;margin-top:52px}
.service{display:flex;gap:18px;align-items:flex-start}
.service-icon{flex:0 0 70px;height:70px;border-radius:50%;background:var(--orange);display:flex;align-items:center;justify-content:center}
.service h3{color:var(--white);font-size:16px;font-weight:700;margin-top:8px}
.service p{color:#d5def0;font-size:11px;line-height:16px;margin-top:6px}

.pricing{height:440px;background:var(--light);position:relative}
.price-table{position:absolute;left:168px;top:50px;display:flex;align-items:flex-start}
.plan{width:216px;background:var(--white);border:1px solid #d9dde5;text-align:left}
.plan-head{height:62px;display:flex;align-items:center;justify-content:center;color:var(--white);font-weight:800;font-size:17px}
.plan.support .plan-head{background:var(--purple)}
.plan.voice .plan-head{background:var(--orange)}
.plan.hosting{margin-top:-22px;box-shadow:0 6px 18px rgba(0,0,0,.25);position:relative;z-index:1}
.plan.hosting .plan-head{background:var(--sky);height:84px}
.plan.cloud .plan-head{background:var(--amber)}
.plan ul{list-style:none;padding:0 22px}
.plan li{font-size:12px;font-weight:700;color:var(--heading);padding:14px 0;border-bottom:1px solid #e3e6ec;line-height:17px}
.plan-cta{display:block;width:110px;margin:18px auto 20px;background:var(--orange);color:var(--white);font-size:11px;font-weight:700;text-align:center;padding:9px 0;text-decoration:none}

.tech-support{height:440px;background:var(--blue);text-align:center;padding-top:94px}
.tech-support .section-title{color:var(--white)}
.tech-support p{color:#d5def0;font-size:13px;line-height:20px;width:880px;margin:26px auto 0}
.btn-outline{display:inline-block;margin-top:30px;border:2px solid var(--white);color:var(--white);font-size:13px;font-weight:700;padding:12px 22px;text-decoration:none}

.expectations{height:280px;text-align:center;padding-top:56px}
.expectations p{font-size:13px;line-height:20px;width:880px;margin:22px auto 0}

.site-footer{height:224px;background:var(--footer);position:relative;color:var(--footer-text)}
.footer-cols{display:grid;grid-template-columns:330px 190px 300px 200px;column-gap:40px;padding:28px 60px 0}
.footer-cols h4{color:var(--white);font-size:18px;font-weight:600;letter-spacing:1px;margin-bottom:14px}
.footer-brand .brand-name{color:var(--white);font-size:28px}
.footer-brand .brand-square{width:26px;height:26px;background:var(--white)}
.footer-brand p{font-size:11px;line-height:17px;margin-top:14px}
.footer-links{list-style:none;font-size:12px;line-height:20px}
.newsletter p{font-size:11px;line-height:17px}
.newsletter-input{margin-top:12px;width:210px;height:30px;background:var(--white);font-size:11px;color:#999;padding:7px 10px}
.newsletter-btn{margin-top:10px;display:inline-block;background:var(--blue);color:var(--white);font-size:11px;padding:6px 14px}
.social-list{list-style:none;font-size:12px}
.social-list li{display:flex;align-items:center;gap:10px;margin-bottom:12px}
.social-dot{width:18px;height:18px;background:var(--sky)}
.footer-bottom{position:absolute;left:0;right:0;bottom:0;height:30px;background:var(--footer-dark);text-align:center;font-size:10px;line-height:30px}
</style>
</head>
<body>

<header class="site-header">
  <div class="brand"><span class="brand-square"></span><span class="brand-name">BRIGHT MEND</span></div>
  <nav class="main-nav">
    <a class="active" href="#">HOME</a><a href="#">SUPPORT</a><a href="#">SERVICES</a><a href="#">ABOUT</a><a href="#">CONTACT</a>
  </nav>
</header>

<section class="hero">
  <h1 class="hero-title">IT SERVICES THE FAIR WAY</h1>
  <div class="hero-art" role="img" aria-label="Flat illustration of laptops, phones, cloud and connected IT devices around a megaphone"></div>
  <span class="slider-arrow prev"><svg width="14" height="20" viewBox="0 0 14 20"><path d="M11 2 3 10l8 8" fill="none" stroke="#fff" stroke-width="3"/></svg></span>
  <span class="slider-arrow next"><svg width="14" height="20" viewBox="0 0 14 20"><path d="M3 2l8 8-8 8" fill="none" stroke="#fff" stroke-width="3"/></svg></span>
</section>

<section class="welcome">
  <h2 class="section-title">WELCOME TO BRIGHT MEND</h2>
  <p>We don't think your local business should pay the earth for IT support you can trust. We keep prices fair and our engineers friendly, so every device, server and call is handled quickly. If you need help with the latest technology, talk to us first.</p>
  <div class="call-line">CALL US TODAY ON 01632 960 418</div>
</section>

<section class="services">
  <h2 class="section-title">OUR SERVICES</h2>
  <div class="service-grid">
    <div class="service"><span class="service-icon"><svg width="34" height="34" viewBox="0 0 34 34"><circle cx="17" cy="11" r="7" fill="#fff"/><path d="M4 32c0-8 6-12 13-12s13 4 13 12z" fill="#fff"/></svg></span><div><h3>SUPPORT</h3><p>Unlimited remote support, monitoring, backup and care from £8.50 a month</p></div></div>
    <div class="service"><span class="service-icon"><svg width="34" height="34" viewBox="0 0 34 34"><path d="M8 3l6 7-3 4c2 4 5 7 9 9l4-3 7 6-4 5C15 30 4 19 3 8z" fill="#fff"/></svg></span><div><h3>VOICE</h3><p>Clear business phone lines, call routing and handsets at honest monthly prices</p></div></div>
    <div class="service"><span class="service-icon"><svg width="34" height="34" viewBox="0 0 34 34"><circle cx="17" cy="17" r="13" fill="none" stroke="#fff" stroke-width="3"/><path d="M4 17h26M17 4c-6 7-6 19 0 26M17 4c6 7 6 19 0 26" fill="none" stroke="#fff" stroke-width="2"/></svg></span><div><h3>INTERNET</h3><p>Fast broadband and leased lines installed, monitored and supported by our team</p></div></div>
    <div class="service"><span class="service-icon"><svg width="34" height="34" viewBox="0 0 34 34"><rect x="7" y="15" width="20" height="15" fill="#fff"/><path d="M11 15v-4a6 6 0 0 1 12 0v4" fill="none" stroke="#fff" stroke-width="3"/></svg></span><div><h3>SECURITY</h3><p>Firewalls, antivirus and patch management keeping your office safe every single day</p></div></div>
    <div class="service"><span class="service-icon"><svg width="34" height="34" viewBox="0 0 34 34"><rect x="6" y="5" width="22" height="9" fill="#fff"/><rect x="6" y="18" width="22" height="9" fill="#fff"/></svg></span><div><h3>HOSTING</h3><p>Reliable web and email hosting with daily backups and friendly expert help</p></div></div>
    <div class="service"><span class="service-icon"><svg width="36" height="34" viewBox="0 0 36 34"><path d="M9 26a7 7 0 0 1 0-14 9 9 0 0 1 17-2 8 8 0 0 1 1 16z" fill="#fff"/></svg></span><div><h3>CLOUD</h3><p>Move files and apps to the cloud and work securely from anywhere</p></div></div>
  </div>
</section>

<section class="pricing">
  <div class="price-table">
    <div class="plan support"><div class="plan-head">SUPPORT</div><ul><li>UNLIMITED MONTHLY REMOTE SUPPORT</li><li>WORKSTATIONS £8.50</li><li>CORVEX NT £28.00</li><li>SERVERS £45.00</li></ul><a class="plan-cta" href="#">GET NOW</a></div>
    <div class="plan voice"><div class="plan-head">VOICE</div><ul><li>UNLIMITED MONTHLY REMOTE SUPPORT</li><li>WORKSTATIONS £8.50</li><li>CORVEX NT £28.00</li><li>SERVERS £45.00</li></ul><a class="plan-cta" href="#">GET NOW</a></div>
    <div class="plan hosting"><div class="plan-head">HOSTING</div><ul><li>UNLIMITED MONTHLY REMOTE SUPPORT</li><li>WORKSTATIONS £8.50</li><li>CORVEX NT £28.00</li><li>SERVERS £45.00</li></ul><a class="plan-cta" href="#">GET NOW</a></div>
    <div class="plan cloud"><div class="plan-head">CLOUD</div><ul><li>UNLIMITED MONTHLY REMOTE SUPPORT</li><li>WORKSTATIONS £8.50</li><li>CORVEX NT £28.00</li><li>SERVERS £45.00</li></ul><a class="plan-cta" href="#">GET NOW</a></div>
  </div>
</section>

<section class="tech-support">
  <h2 class="section-title">TECHNICAL SUPPORT</h2>
  <p>Our engineers are on hand to fix problems fast, either remotely or on site. Whether it is a single laptop or a whole network, we keep your business running with clear, fixed monthly costs and no surprises.</p>
  <a class="btn-outline" href="#">CONTACT US</a>
</section>

<section class="expectations">
  <h2 class="section-title">WE EXCEED EXPECTATIONS</h2>
  <p>As the local IT support company and trusted Managed Service Provider, we go further for every client, responding quickly and treating your systems as carefully as our own.</p>
  <div class="call-line">CALL US TODAY ON 01632 960 418</div>
</section>

<footer class="site-footer">
  <div class="footer-cols">
    <div class="footer-brand">
      <div class="brand"><span class="brand-square"></span><span class="brand-name">BRIGHT MEND</span></div>
      <p>Value-priced IT support for small offices and growing teams. Fixed monthly costs, friendly engineers and fast remote help whenever you need it.</p>
    </div>
    <div><h4>LEGAL</h4><ul class="footer-links"><li>Terms of Service</li><li>Privacy Policy</li><li>Regulation</li></ul></div>
    <div class="newsletter"><h4>NEWSLETTER</h4><p>Do you want to get email updates from us? Sign up below.</p><div class="newsletter-input">Your email</div><span class="newsletter-btn">Submit</span></div>
    <div><h4>SOCIAL</h4><ul class="social-list"><li><span class="social-dot"></span>Chatterly</li><li><span class="social-dot"></span>Tweetline</li><li><span class="social-dot"></span>Linkpile</li></ul></div>
  </div>
  <div class="footer-bottom">© 2015 Bright Mend Ltd. All rights reserved.</div>
</footer>

</body>
</html>
```